Consumer and commercial IOT solutions (Internet Of Things)

We are a startup and are looking for business cards with logo. The logo will appear on all of our media as well as our ecommerce site and social sites that have yet to be developed. We want to present a fresh face on a high tech company that innovates at every turn. You can read about our solutions on our information only web site www.plonaxhub.net - We have some wording we would like used on our business cards but there is no place for this except for here. The company name is "RM Industrial IOT" I have some samples of logos I am interested in seeing but I will let your team make the initial presentations

```html
<!DOCTYPE html>
<html lang="en">
<head>
<meta charset="utf-8">
<title>RM Industrial IOT – Business Card</title>
<link rel="stylesheet" href="https://fonts.googleapis.com/css2?family=Arimo:wght@400;700&display=swap">
<style>
  :root {
    --backdrop: #e4e4e4;
    --card-dark: #231f20;
    --card-light: #ffffff;
    --accent: #f26a2a;
    --ink: #231f20;
    --ink-light: #ffffff;
    --shadow: rgba(0,0,0,0.35);
  }
  * { box-sizing: border-box; margin: 0; padding: 0; }
  html, body {
    width: 1200px; height: 900px; overflow: hidden;
    background: var(--backdrop);
    font-family: "Arimo", Arial, sans-serif;
  }
  .stage { position: relative; width: 1200px; height: 900px; }
  .card {
    position: absolute; top: 216px;
    width: 309px; height: 501px;
    box-shadow: 2px 3px 4px var(--shadow);
  }
  .card--front {
    left: 279px; background: var(--card-dark);
    border-radius: 0 68px 0 68px;
  }
  .card--back {
    left: 617px; background: var(--card-light);
    border-radius: 68px 0 68px 0;
  }
  .brand {
    position: absolute; left: 0; right: 0;
    display: flex; flex-direction: column; align-items: center;
  }
  .brand__dot {
    width: 22px; height: 22px; border-radius: 50%;
    background: var(--accent); margin-bottom: 26px;
  }
  .brand__name {
    font-size: 24px; font-weight: 400; letter-spacing: 0.5px;
    white-space: nowrap;
  }
  .card--front .brand { top: 170px; }
  .card--front .brand__name { color: var(--ink-light); }
  .card--back .brand { top: 96px; }
  .card--back .brand__name { color: var(--ink); }
  .front-url {
    position: absolute; left: 0; right: 0; top: 445px;
    text-align: center; color: var(--accent);
    font-size: 14px; letter-spacing: 1.2px;
  }
  .contact { position: absolute; left: 32px; top: 308px; color: var(--ink); }
  .contact__name {
    color: var(--accent); font-weight: 700; font-size: 21px; line-height: 1;
  }
  .contact__role { font-size: 14px; margin-top: 3px; }
  .contact__list { list-style: none; margin-top: 15px; font-size: 14px; }
  .contact__list li { display: flex; align-items: center; height: 18px; }
  .contact__list svg { width: 13px; height: 13px; margin-right: 5px; fill: var(--accent); }
  .contact__list .accent { color: var(--accent); }
  .contact__address { margin-top: 14px; font-size: 14px; line-height: 18px; }
</style>
</head>
<body>
<main class="stage">
  <section class="card card--front">
    <div class="brand">
      <span class="brand__dot"></span>
      <span class="brand__name">RM INDUSTRIAL IOT</span>
    </div>
    <p class="front-url">www.corvellane.ca</p>
  </section>

  <section class="card card--back">
    <div class="brand">
      <span class="brand__dot"></span>
      <span class="brand__name">RM INDUSTRIAL IOT</span>
    </div>
    <div class="contact">
      <p class="contact__name">DANIEL PORTER</p>
      <p class="contact__role">Managing Director</p>
      <ul class="contact__list">
        <li><svg viewBox="0 0 24 24"><path d="M6.6 10.8a15 15 0 0 0 6.6 6.6l2.2-2.2a1 1 0 0 1 1-.25 11.4 11.4 0 0 0 3.6.57 1 1 0 0 1 1 1V20a1 1 0 0 1-1 1A17 17 0 0 1 3 4a1 1 0 0 1 1-1h3.5a1 1 0 0 1 1 1c0 1.25.2 2.45.57 3.6a1 1 0 0 1-.25 1z"/></svg>044-987 650 312</li>
        <li><svg viewBox="0 0 24 24"><path d="M2 5h20v14H2z M2 5l10 8 10-8" /></svg>hello@rmiot-mail.com</li>
        <li><svg viewBox="0 0 24 24"><circle cx="12" cy="12" r="10"/></svg>www.<span class="accent">rmiotlink</span>.com</li>
      </ul>
      <p class="contact__address">421, Address line goes here<br>45452,Country Name</p>
    </div>
  </section>
</main>
</body>
</html>
```